Calder Aviation website

We are an aviation company based in Miramar, FL but with worldwide coverage. We are involved in commercial aircraft (mostly freighters) trading, sale & leasing. Specifically, we specialized in freighters of the Veltram family (V316, V328, V335, V342, V359). We also assist with financing, sale/leaseback. Handle special aviation projects and provide consultancy services. Currently engaged in a Veltram 359 passenger to Freighter conversion (P2F).

Website Preliminary Initial Content/Sections as follows:

About Us
Founded in 2011, Calder Aviation's management has many years of experience in Aviation, a strong background in scheduled airlines with emphasis in all cargo operations, freight forwarding supply chain and freight logistics, as well as ACMI and CMI operations.

Calder’s focuses in facilitating wet and dry lease operations, charter and ACMI programs consultancy, aircraft sales, leasing and procurement, aviation consultancy and aircraft management.

Calder team is a hands-on reliable alternative that works toward achieving your aircraft and aviation objectives by meeting your requirements and timeframe throughout professional and personalized service.

Tiberio Salcedo has over three decades of experience in the aviation field including aircraft maintenance, airline management, supply chain and logistics management. Tiberio is a true entrepreneur with proven experience and expertise on the multiple facets of the commercial aviation industry throughout the creation and development of a cluster of aviation entities. Tiberio is the founder and former sole member/chairman of 64 Air, a Veltram 342 All-Cargo U.S. Certificated Air Carrier created from scratch in 2014 which nowadays conforms a superb growing airline platform with an immaculate compliance operational record.

Services

Aircraft Finance, Trading, Procurement and Leasing
Calder buys, sells, leases and facilitates aircraft trading while specializes in structured aircraft investment projects. Calder has deep industry relationships and years of expertise, allowing to successfully execute lease transactions. We assist airlines, financial institutions and leasing companies when selling or purchasing aircraft.

Aircraft Available for Sale/Lease

Sale/Leaseback
Sale-leaseback is a method of financing. If your company needs liquidity, your aircraft or engine can serve as collateral for a loan throughout a sale-leaseback transaction. Sale-leaseback can free the equity tied up in aircraft or asset. Even if there is no pressing need for funds, a sale-leaseback allows you to use the equity tied up in your aircraft in a more productive fashion. Leaseback arrangements are usually employed because they confer financing, accounting or taxation benefits.

Passenger to Freighter Conversion (P2F)
Pandemic has seen the resurgence of operators packing freight into the main cabins of passenger aircraft. Carriers have been allowed to transport cargo in the cabin by removing passenger seats completely. NAB/CARO have established exemptions that allow operators to fly in “Preighter” configuration for a limited time. Calder is closely working with a U.S. group that is developing a Class E Supplemental Type Certificate (STC) for applicability on V359 aircraft which will include a cargo door for containerized freight. Final approvals are expected during first quarter of 2022.
Wet lease
Throughout our deep relationships within the industry, Calder facilitates short or long-term wet leases to airlines and qualified parties around the globe, whereby we provide the Aircraft, Crews, Maintenance and Insurance (ACMI) worldwide services at competitive rates. We also specialize in AM leases where the aircraft is registered onto Lessee´s AOC with all maintenance services included in the rates, covering all maintenance risks, or CM or CMI where the client provides the aircraft.

Dry Lease
We offer aircraft from our own portfolio on dry lease or could engage in procuring the aircraft of your choice.

Asset & Aircraft Management
We provide aircraft owners Aircraft Management services, where we manage the technical side of the aircraft or the asset. Calder also provides Harlow Dynamics engines trading, repair and full management services. We also buy Veltram/Skylane surplus inventory.

Worldwide Charters
We facilitate the arrangement of full charters to airlines and logistics companies. Certain territory restrictions may apply.

Aviation Consultancy
We provide airline consultancy services for new or special projects. Calder also specializes on All Cargo International route analysis, implementation and development. Our team provides professional guidance in obtaining worldwide both scheduled and charter authority.

Target Market(s)

Our target market are the airlines, logistics companies and commercial aviation related entities

Industry/Entity Type

Commercial Aviation

Coding

Coded - Design and coding required

Number of Pages Required

3 page

Requirements
Must have
• Illustrations of wide body freighters such V359, V342, V328

```html
<!DOCTYPE html>
<html lang="en">
<head>
<meta charset="utf-8">
<title>Calder Aviation</title>
<link href="https://fonts.googleapis.com/css2?family=Roboto:wght@400;500;700&display=swap" rel="stylesheet">
<style>
:root{
  --navy:#0c1a3d;
  --navy-2:#132652;
  --ink:#111;
  --muted:#555;
  --soft:#8a8a8a;
  --link:#2f4fa3;
  --line:#e3e3e3;
  --white:#fff;
}
*{box-sizing:border-box;margin:0;padding:0}
html,body{width:1200px;height:4065px;overflow:hidden}
body{font-family:"Roboto",Arial,sans-serif;color:var(--ink);background:var(--white);position:relative}
.abs{position:absolute}
a{color:inherit;text-decoration:none}

/* nav */
.nav{position:absolute;top:0;left:0;width:1200px;height:66px;background:var(--navy);color:var(--white)}
.brand{position:absolute;left:152px;top:12px;text-align:center;width:130px}
.brand .name{font-size:19px;letter-spacing:1px;font-weight:400}
.brand .sub{font-size:8px;letter-spacing:7px;margin-top:2px}
.menu{position:absolute;left:347px;top:23px;display:flex;gap:38px;font-size:15px}
.search{position:absolute;left:886px;top:17px;width:31px;height:31px;border-radius:50%;background:#2b3f9a}
.login{position:absolute;left:952px;top:11px;width:113px;height:41px;border:1.5px solid #cfd4e0;border-radius:4px;display:flex;align-items:center;justify-content:center;gap:8px;font-weight:700;font-size:15px}

/* hero */
.hero{position:absolute;top:66px;left:0;width:1200px;height:591px;background:linear-gradient(180deg,#3d5f8c 0%,#8aa4c2 45%,#b9c6d4 70%,#4c5838 86%,#3a4a2c 100%)}
.hero h1{position:absolute;left:110px;top:166px;color:var(--white);font-size:40px;font-weight:500;letter-spacing:.5px}
.hero p{position:absolute;left:111px;top:220px;color:#eef1f6;font-size:15px;line-height:26px;width:380px}
.btn{display:inline-flex;align-items:center;gap:10px;background:var(--navy);color:var(--white);font-weight:700;font-size:14px;border-radius:3px}
.hero .btn{position:absolute;left:111px;top:288px;height:48px;padding:0 18px}
.arrow-btn{position:absolute;top:300px;width:38px;height:38px;border-radius:50%;background:var(--white);display:flex;align-items:center;justify-content:center}

/* titles */
.title{position:absolute;left:0;width:1200px;text-align:center;font-size:34px;font-weight:700;color:var(--ink)}

/* service cards */
.svc{position:absolute;top:811px;width:314px;height:314px;background:var(--white);box-shadow:0 2px 8px rgba(0,0,0,.15)}
.svc .photo{height:205px;background:linear-gradient(180deg,#4f7fbf,#b8cde6 70%,#8aa36b)}
.svc .badge{position:absolute;left:111px;top:161px;width:92px;height:92px;border-radius:50%;background:var(--white);border:2px solid #e6e6e6;display:flex;align-items:center;justify-content:center}
.svc h3{position:absolute;top:268px;left:0;width:100%;text-align:center;font-size:16px;font-weight:500}

/* about */
.about{position:absolute;top:1211px;left:0;width:1200px;height:535px;background:linear-gradient(180deg,#7f9ec6,#b6c8dd 55%,#9aa3a0 80%,#7a6a4c)}
.about .box{position:absolute;left:560px;top:85px;width:528px;height:365px;background:var(--white);padding:26px 32px}
.about h2{font-size:34px;font-weight:700;margin-bottom:14px}
.about p{font-size:15px;line-height:26.5px;color:#222}
.about .btn{margin-top:20px;height:48px;padding:0 18px}

/* aircraft grid */
.feat{position:absolute;width:290px;text-align:center}
.feat svg{display:block;margin:0 auto}
.feat h4{font-size:15px;font-weight:500;margin-top:12px;line-height:20px}
.feat p{font-size:13.5px;line-height:23px;color:#333;margin-top:8px}
.feat .more{display:inline-flex;align-items:center;gap:8px;font-size:13px;font-weight:700;color:var(--navy);margin-top:10px}
.feat.boxed{border:1px solid var(--line);box-shadow:0 1px 6px rgba(0,0,0,.08);padding-top:28px;height:274px}

/* blog */
.blog{position:absolute;top:2597px;left:0;width:1200px;height:608px;background:linear-gradient(180deg,#0f1f4a,#132858 60%,#0e1c44)}
.blog .title{color:var(--white);top:66px}
.post{position:absolute;top:152px;width:303px;height:382px;background:var(--white)}
.post .photo{height:171px;background:linear-gradient(180deg,#8fb0d6,#d9e3ec 60%,#8e9c82)}
.post .meta{display:flex;gap:34px;font-size:14px;color:var(--link);padding:16px 22px 0}
.post .meta span{display:flex;align-items:center;gap:8px}
.post h5{font-size:13.5px;font-weight:700;line-height:22px;padding:8px 22px 0}
.post p{font-size:13.5px;color:var(--soft);line-height:23px;padding:8px 22px 0}
.post .read{display:flex;align-items:center;gap:10px;font-size:14px;font-weight:700;padding:12px 22px 0}

/* contact */
.field{position:absolute;border:1.5px solid #cfcfcf;border-radius:3px;font-size:13px;color:#222;padding:9px 13px}
.submit{position:absolute;left:529px;top:3564px;width:142px;height:42px;justify-content:center}

/* footer */
.footer{position:absolute;top:3692px;left:0;width:1200px;height:373px;background:var(--navy);color:var(--white)}
.footer .logo{position:absolute;left:110px;top:62px;width:232px;text-align:center}
.footer .logo .name{font-size:33px;letter-spacing:2px}
.footer .logo .sub{font-size:16px;letter-spacing:15px;margin-top:4px}
.footer .about-t{position:absolute;left:110px;top:150px;width:240px;font-size:15px;line-height:23px}
.social{position:absolute;left:110px;top:247px;display:flex;gap:14px}
.social span{width:33px;height:33px;border:1.5px solid #fff;border-radius:50%;display:flex;align-items:center;justify-content:center}
.social span i{width:9px;height:9px;background:#fff;border-radius:50%}
.fcol{position:absolute;top:66px}
.fcol h6{font-size:15px;font-weight:700;padding-bottom:9px;position:relative}
.fcol h6::after{content:"";position:absolute;left:0;bottom:0;width:36px;height:2px;background:#fff}
.fcol ul{list-style:none;margin-top:16px}
.fcol li{font-size:15px;height:38.5px}
.fcol li::before{content:"»";margin-right:12px}
.ci{display:flex;gap:16px;margin-top:18px;font-size:15px;line-height:22px}
.ci .ico{width:32px;height:32px;border-radius:50%;background:#2a3656;flex:none;display:flex;align-items:center;justify-content:center}
.ci b{font-size:12px;display:block}
.copy{position:absolute;left:110px;top:317px;width:980px;border-top:1px solid #3a4668;text-align:center;font-size:13px;padding-top:18px}
</style>
</head>
<body>
<svg width="0" height="0" style="position:absolute">
  <defs>
    <symbol id="plane" viewBox="0 0 24 24"><path d="M21 16v-2l-8-5V3.5a1.5 1.5 0 0 0-3 0V9l-8 5v2l8-2.5V19l-2 1.5V22l3.5-1 3.5 1v-1.5L13 19v-5.5z" fill="currentColor"/></symbol>
    <symbol id="circ-arrow" viewBox="0 0 16 16"><circle cx="8" cy="8" r="7" fill="currentColor"/><path d="M6.5 4.5 10 8l-3.5 3.5" stroke="#fff" stroke-width="2" fill="none"/></symbol>
  </defs>
</svg>

<header class="nav">
  <div class="brand"><div class="name">CALDER</div><div class="sub">AVIATION</div></div>
  <nav class="menu"><a>HOME</a><a>ABOUT US</a><a>SERVICES</a><a>BLOG</a><a>CONTACT US</a></nav>
  <div class="search"><svg width="31" height="31" viewBox="0 0 31 31"><circle cx="14" cy="14" r="5" stroke="#fff" stroke-width="2" fill="none"/><path d="M17.5 17.5l4 4" stroke="#fff" stroke-width="2.5"/></svg></div>
  <div class="login">LOGIN <svg width="16" height="14" viewBox="0 0 16 14"><path d="M1 7h8M6 3.5 9.5 7 6 10.5M11 1h4v12h-4" stroke="#fff" stroke-width="2" fill="none"/></svg></div>
</header>

<section class="hero" role="img" aria-label="Wide body freighter landing over green fields under a cloudy blue sky">
  <h1>CALDER AVIATION</h1>
  <p>We assist airlines,financial institutions and leasing companies when selling or purchasing aircraft.</p>
  <a class="btn">LEARN MORE <svg width="16" height="16" style="color:#fff"><use href="#circ-arrow"/></svg></a>
  <div class="arrow-btn" style="left:37px"><svg width="14" height="14" viewBox="0 0 14 14"><path d="M9 2 4 7l5 5" stroke="#111" stroke-width="2" fill="none"/></svg></div>
  <div class="arrow-btn" style="left:1125px"><svg width="14" height="14" viewBox="0 0 14 14"><path d="M5 2l5 5-5 5" stroke="#111" stroke-width="2" fill="none"/></svg></div>
</section>

<h2 class="title" style="top:735px">OUR SERVICES</h2>
<div class="svc" style="left:109px"><div class="photo" role="img" aria-label="Airliner climbing against blue sky and clouds"></div><div class="badge"><svg width="54" height="54" style="transform:rotate(90deg)"><use href="#plane"/></svg></div><h3>AIRCRAFT FINANCE</h3></div>
<div class="svc" style="left:443px"><div class="photo" role="img" aria-label="Airliner taking off over a green field"></div><div class="badge"><svg width="54" height="54" style="transform:rotate(45deg)"><use href="#plane"/></svg></div><h3>TRADING</h3></div>
<div class="svc" style="left:776px"><div class="photo" role="img" aria-label="Wide body aircraft on the runway"></div><div class="badge"><svg width="54" height="54" style="transform:rotate(45deg)"><use href="#plane"/></svg></div><h3>PROCUREMENT AND LEASING</h3></div>

<section class="about" role="img" aria-label="Wide body jet climbing out over an airport apron">
  <div class="box">
    <h2>ABOUT US</h2>
    <p>Founded in 2011, Calder Aviation's management has many years of experience in Aviation,a strong background in scheduled airlines with emphasis in all cargo operations, freight forwarding supply chain and freight logistics, as well as ACMI and CMI operations. Calder’s focuses in facilitating wet and dry lease operations, charter and ACMI programs consultancy,aircraft sales, leasing and procurement, aviation consultancy and aircraft managment.</p>
    <a class="btn">LEARN MORE <svg width="16" height="16" style="color:#fff"><use href="#circ-arrow"/></svg></a>
  </div>
</section>

<h2 class="title" style="top:1822px;line-height:37px">AIRCRAFT AVAILABLE FOR<br>SALE/LEASE</h2>

<div class="feat" style="left:145px;top:1960px"><svg width="80" height="80" style="color:var(--navy);transform:rotate(45deg)"><use href="#plane"/></svg><h4>SALE/LEASEBACK</h4><p>Leaseback arrangements are usually employed because they confer financing, accounting ortaxation benefits.</p><a class="more">READ MORE <svg width="14" height="14" style="color:var(--navy)"><use href="#circ-arrow"/></svg></a></div>
<div class="feat boxed" style="left:455px;top:1937px;width:290px"><svg width="110" height="64" viewBox="0 0 110 64" style="color:var(--navy)"><path d="M6 10h12l14 16h50c12 0 22 4 22 8s-10 8-22 8H20z" fill="currentColor"/><rect x="38" y="28" width="40" height="4" fill="#fff"/><path d="M48 42 60 60h8l-6-18z" fill="currentColor"/></svg><h4>PASSENGER TO FREIGHTER<br>CONVERSION (P2F)</h4><p>Final approvals are expected during<br>first quarter of 2022.</p><a class="more">READ MORE <svg width="14" height="14" style="color:var(--navy)"><use href="#circ-arrow"/></svg></a></div>
<div class="feat" style="left:766px;top:1960px"><svg width="80" height="80" style="color:var(--navy);transform:rotate(-45deg)"><use href="#plane"/></svg><h4>DRY LEASE</h4><p>We offer aircraft from our own portfolio on dry lease or could engage in procuring the aircraft of your choice.</p><a class="more">READ MORE <svg width="14" height="14" style="color:var(--navy)"><use href="#circ-arrow"/></svg></a></div>

<div class="feat" style="left:143px;top:2260px"><svg width="120" height="80" style="color:var(--navy);transform:rotate(90deg)"><use href="#plane"/></svg><h4>AIRCRAFT MANAGEMENT</h4><p>Calder also provides Harlow Dynamics engines trading, repair and full management services.</p><a class="more">READ MORE <svg width="14" height="14" style="color:var(--navy)"><use href="#circ-arrow"/></svg></a></div>
<div class="feat" style="left:455px;top:2260px"><svg width="80" height="80" style="color:var(--navy)"><use href="#plane"/></svg><h4>WORLDWIDE CHARTERS</h4><p>We facilitate the arrangement of full charters to airlines and logistics companies.Certain territory</p><a class="more">READ MORE <svg width="14" height="14" style="color:var(--navy)"><use href="#circ-arrow"/></svg></a></div>
<div class="feat" style="left:766px;top:2262px"><svg width="100" height="80" style="color:var(--navy);transform:rotate(90deg)"><use href="#plane"/></svg><h4>AVIATION CONSULTANCY</h4><p>Calder also specializes on All Cargo International route analysis, implementation and development.</p><a class="more">READ MORE <svg width="14" height="14" style="color:var(--navy)"><use href="#circ-arrow"/></svg></a></div>

<section class="blog">
  <h2 class="title">OUR BLOG</h2>
  <article class="post" style="left:122px"><div class="photo" role="img" aria-label="Airliner flying through white clouds"></div>
    <div class="meta"><span>↪ Share</span><span>▭ Comments</span></div>
    <h5>LOREM IPSUM DOLOR AMET EIUSMOD CONSECTETUR ADIPISCING SIT ELIT</h5>
    <p>Lorem ipsum sitconsectetur adipiscing elit, sed do eiusmod tempor incididunt dolore magna tempor incididunt aliqua.</p>
    <a class="read">Read More <svg width="14" height="14" style="color:var(--ink)"><use href="#circ-arrow"/></svg></a></article>
  <article class="post" style="left:448px"><div class="photo" role="img" aria-label="Jumbo jet taxiing on a runway"></div>
    <div class="meta"><span>↪ Share</span><span>▭ Comments</span></div>
    <h5>LOREM IPSUM DOLOR AMET EIUSMOD CONSECTETUR ADIPISCING SIT ELIT</h5>
    <p>Lorem ipsum sitconsectetur adipiscing elit, sed do eiusmod tempor incididunt dolore magna tempor incididunt aliqua.</p>
    <a class="read">Read More <svg width="14" height="14" style="color:var(--ink)"><use href="#circ-arrow"/></svg></a></article>
  <article class="post" style="left:775px"><div class="photo" role="img" aria-label="Freighter flying low over hills"></div>
    <div class="meta"><span>↪ Share</span><span>▭ Comments</span></div>
    <h5>LOREM IPSUM DOLOR AMET EIUSMOD CONSECTETUR ADIPISCING SIT ELIT</h5>
    <p>Lorem ipsum sitconsectetur adipiscing elit, sed do eiusmod tempor incididunt dolore magna tempor incididunt aliqua.</p>
    <a class="read">Read More <svg width="14" height="14" style="color:var(--ink)"><use href="#circ-arrow"/></svg></a></article>
</section>

<h2 class="title" style="top:3285px">GET IN TOUCH</h2>
<div class="field" style="left:223px;top:3349px;width:376px;height:35px">First Name:</div>
<div class="field" style="left:612px;top:3349px;width:365px;height:35px">Email:</div>
<div class="field" style="left:223px;top:3403px;width:376px;height:35px">Phone Number:</div>
<div class="field" style="left:612px;top:3403px;width:365px;height:35px">Address:</div>
<div class="field" style="left:223px;top:3456px;width:754px;height:74px">Message:</div>
<a class="btn submit">SUBMIT <svg width="16" height="16" style="color:#fff"><use href="#circ-arrow"/></svg></a>

<footer class="footer">
  <div class="logo"><div class="name">CALDER</div><div class="sub">AVIATION</div></div>
  <p class="about-t">freight forwarding supply chain and freight logistics, as well as ACMI and CMI operations.</p>
  <div class="social"><span><i></i></span><span><i></i></span><span><i></i></span><span><i></i></span></div>
  <div class="fcol" style="left:450px"><h6>QUICKLINKS</h6><ul><li>Home</li><li>About Us</li><li>Services</li><li>Blog</li><li>contact us</li></ul></div>
  <div class="fcol" style="left:648px"><h6>OTHERLINKS</h6><ul><li>FAQ</li><li>Services</li><li>Team</li><li>Privacy</li><li>Policy</li></ul></div>
  <div class="fcol" style="left:852px;width:260px"><h6>CONTACT US</h6>
    <div class="ci"><span class="ico"><svg width="14" height="14" viewBox="0 0 14 14"><path d="M3 1l2.5 3-1.5 1.5c1 2 2.5 3.5 4.5 4.5L10 8.5l3 2.5-1.5 2C6 13 1 8 1 2.5z" fill="#fff"/></svg></span><div><b>Phone Number :</b>555-014-7720</div></div>
    <div class="ci"><span class="ico"><svg width="14" height="12" viewBox="0 0 14 12"><rect x="1" y="1" width="12" height="10" fill="none" stroke="#fff" stroke-width="1.5"/><path d="M1 1l6 5 6-5" fill="none" stroke="#fff" stroke-width="1.5"/></svg></span><div><b>Email:</b>info@calderaviation.com</div></div>
    <div class="ci"><span class="ico"><svg width="12" height="16" viewBox="0 0 12 16"><path d="M6 1a5 5 0 0 1 5 5c0 4-5 9-5 9S1 10 1 6a5 5 0 0 1 5-5z" fill="#fff"/><circle cx="6" cy="6" r="2" fill="#2a3656"/></svg></span><div><b>Address :</b>122,Lorem ipsum dolor amt consectetur adipiscing elit</div></div>
  </div>
  <div class="copy">©Copyrights 2021 &nbsp;Calder Aviation | &nbsp; All Rights Reserved &nbsp;|</div>
</footer>
</body>
</html>
```